Stylish new business card needed!

Hello everyone! I am in need of a new business card design for an alarm company here in Hurricane WV. I have all fonts, color codes and logos provided for you use! We are a young company and like the style of a clean sleek looking business card. Would like it double sided, one side holding the logo and the other with your design!
Target Market(s)
The people that are looking for the newest tech for home automation and security
Industry/Entity Type
Alarm services; Home automation
Contact Information for Business Card
Name of person; position (Sales; Installer); Phone Number (555.418.7260); Employee cell Number; Website (www.GuardedByVelk.example); Employee Email; Double sided
Look and feel
Each slider illustrates characteristics of the customer's brand and the style your logo design should communicate.

```html
<!DOCTYPE html>
<html lang="en">
<head>
<meta charset="utf-8">
<title>Velk Business Card</title>
<link href="https://fonts.googleapis.com/css2?family=Montserrat:wght@800;900&family=Arimo:wght@400;700&display=swap" rel="stylesheet">
<style>
  :root {
    --orange: #f28f50;
    --grey: #9a9a9a;
    --ink: #1c1c1c;
    --paper: #ffffff;
    --backdrop: #e9e7e4;
  }
  * { margin: 0; padding: 0; box-sizing: border-box; }
  html, body { width: 1200px; height: 900px; overflow: hidden; }
  body {
    background: var(--backdrop);
    display: flex;
    flex-direction: column;
    align-items: center;
    justify-content: center;
    gap: 40px;
    font-family: "Arimo", Arial, sans-serif;
  }
  .card {
    position: relative;
    width: 700px;
    height: 400px;
    overflow: hidden;
    box-shadow: 0 6px 20px rgba(0,0,0,0.18);
  }

  /* Front side */
  .card-front {
    background: var(--orange);
    color: var(--paper);
    display: flex;
    flex-direction: column;
    align-items: center;
    justify-content: center;
  }
  .front-name {
    font-family: "Montserrat", Arial, sans-serif;
    font-weight: 800;
    font-size: 150px;
    letter-spacing: 6px;
    line-height: 1;
  }
  .front-tagline {
    margin-top: 14px;
    font-family: "Montserrat", Arial, sans-serif;
    font-weight: 800;
    font-size: 13px;
    letter-spacing: 3px;
    text-transform: uppercase;
  }

  /* Back side */
  .card-back { background: var(--paper); color: var(--ink); }
  .name-marker {
    position: absolute;
    top: 128px;
    left: 40px;
    width: 10px;
    height: 56px;
    background: var(--orange);
  }
  .footer-rule {
    position: absolute;
    left: 0;
    right: 0;
    bottom: 44px;
    height: 4px;
    background: var(--grey);
  }
  .footer-band {
    position: absolute;
    left: 0;
    right: 0;
    bottom: 0;
    height: 34px;
    background: var(--orange);
  }
  .brand-name {
    position: absolute;
    top: 38px;
    right: 60px;
    font-family: "Montserrat", Arial, sans-serif;
    font-weight: 800;
    font-size: 92px;
    letter-spacing: 4px;
    color: var(--grey);
    line-height: 1;
  }
  .person {
    position: absolute;
    top: 130px;
    left: 50px;
    padding-left: 16px;
  }
  .person-name {
    font-family: "Montserrat", Arial, sans-serif;
    font-weight: 900;
    font-size: 30px;
    letter-spacing: 2px;
    color: var(--orange);
    text-transform: uppercase;
    line-height: 1.05;
  }
  .person-name .first { color: var(--grey); }
  .person-role { font-size: 20px; margin-top: 4px; }
  .address {
    position: absolute;
    top: 190px;
    right: 60px;
    text-align: right;
    font-size: 17px;
    line-height: 1.3;
  }
  .contacts {
    position: absolute;
    top: 224px;
    left: 66px;
    list-style: none;
    font-size: 19px;
    line-height: 1.42;
  }
  .contacts li { display: flex; align-items: center; gap: 12px; }
  .contacts svg { width: 17px; height: 17px; flex: none; }
</style>
</head>
<body>

  <section class="card card-front" aria-label="Card front">
    <div class="front-name">VELK</div>
    <div class="front-tagline">Automation and Security Services</div>
  </section>

  <section class="card card-back" aria-label="Card back">
    <div class="name-marker" aria-hidden="true"></div>
    <div class="footer-rule" aria-hidden="true"></div>
    <div class="footer-band" aria-hidden="true"></div>

    <div class="brand-name">VELK</div>

    <div class="person">
      <div class="person-name"><span class="first">Mark</span> Ellison</div>
      <div class="person-role">Sales; Installer</div>
    </div>

    <div class="address">2480 Orchard Ave, Ste<br>200, Hillview, TX 75990</div>

    <ul class="contacts">
      <li>
        <svg viewBox="0 0 20 20"><path d="M2 8 Q10 1 18 8 L15 10 L13 7 Q10 6 7 7 L5 10 Z M5 11 H15 V17 H5 Z" fill="var(--orange)"/></svg>
        555.418.7260
      </li>
      <li>
        <svg viewBox="0 0 20 20"><rect x="5" y="1.5" width="10" height="17" rx="2" fill="none" stroke="var(--orange)" stroke-width="2"/><circle cx="10" cy="15" r="1.2" fill="var(--orange)"/></svg>
        555.418.7269
      </li>
      <li>
        <svg viewBox="0 0 20 20"><rect x="1" y="4" width="18" height="12" fill="var(--orange)"/><path d="M1 4 L10 11 L19 4" fill="none" stroke="#fff" stroke-width="1.5"/></svg>
        info@GuardedByVelk.example
      </li>
      <li>
        <svg viewBox="0 0 20 20"><circle cx="10" cy="10" r="9" fill="var(--orange)"/><path d="M1 10 H19 M10 1 Q5 10 10 19 M10 1 Q15 10 10 19" fill="none" stroke="#fff" stroke-width="1.2"/></svg>
        www.GuardedByVelk.example
      </li>
    </ul>
  </section>

</body>
</html>
```